Unique Reno7 Property Bussiness Card Design

www.reno7.com.au

Please see website for Company profile. We require a design that incorporates our logo colours and is unique in shape and style compared to all other business cards.

www.reno7.com.au

INSPIRE US !!!
Updates

Target Market(s)

Facility managers, Building Managers, Architects

Industry/Entity Type

Business

Contact Information for Business Card

Reno7 Property Services
Project Manager
Dean Harwoodson
0437 916 204
Sales@reno7.com.au

Logo Text

Reno7 Property Services

Logo styles of interest
Abstract Logo
Requirements
Nice to have
• Card must show we are an established big business to trust.

```html
<!DOCTYPE html>
<html lang="en">
<head>
<meta charset="utf-8">
<title>Reno7 Property Services — Business Card</title>
<link rel="stylesheet" href="https://fonts.googleapis.com/css2?family=Source+Sans+3:wght@400;700&display=swap">
<style>
  :root {
    --page-bg: #d9d9d9;
    --brand-red: #c0232a;
    --brand-red-deep: #a61c22;
    --brand-orange: #ea6a22;
    --brand-orange-soft: #f08a3a;
    --card-white: #ffffff;
    --ink-dark: #2b2b2b;
  }
  * { box-sizing: border-box; margin: 0; padding: 0; }
  html, body {
    width: 1200px;
    height: 1044px;
    overflow: hidden;
    background: var(--page-bg);
    font-family: "Source Sans 3", "Myriad Pro", Arial, sans-serif;
  }
  .card-sheet {
    position: relative;
    width: 1200px;
    height: 1044px;
  }
  .card {
    position: absolute;
    top: 370px;
    width: 540px;
    height: 305px;
    border-radius: 22px;
    overflow: hidden;
    box-shadow: 0 4px 14px rgba(0,0,0,0.25);
  }
  /* Back side */
  .card-back {
    left: 40px;
    background: radial-gradient(ellipse at 48% 38%, var(--brand-orange-soft) 0%, var(--brand-orange) 28%, var(--brand-red) 70%, var(--brand-red-deep) 100%);
  }
  .card-back .back-glow {
    position: absolute;
    left: 150px;
    top: 20px;
    width: 240px;
    height: 220px;
    border-radius: 50%;
    background: radial-gradient(circle, rgba(255,170,110,0.35) 0%, rgba(255,170,110,0) 70%);
  }
  .card-back .back-website {
    position: absolute;
    left: 0;
    right: 0;
    bottom: 22px;
    text-align: center;
    color: var(--card-white);
    font-size: 14px;
  }
  /* Front side */
  .card-front {
    left: 620px;
    background: var(--card-white);
  }
  .front-brand {
    position: absolute;
    left: 44px;
    top: 94px;
    display: flex;
    align-items: center;
    gap: 8px;
  }
  .front-brand .brand-square {
    width: 22px;
    height: 22px;
    background: var(--brand-red);
  }
  .front-brand .brand-name {
    font-size: 27px;
    font-weight: 700;
    color: var(--ink-dark);
    letter-spacing: 0.2px;
  }
  .front-person {
    position: absolute;
    left: 354px;
    top: 86px;
    font-size: 15px;
    line-height: 19px;
  }
  .front-person .person-name { color: var(--brand-red); }
  .front-person .person-role { color: var(--brand-orange); }
  .front-waves {
    position: absolute;
    left: 0;
    top: 0;
    width: 540px;
    height: 305px;
  }
  .front-contact {
    position: absolute;
    right: 30px;
    bottom: 22px;
    display: flex;
    gap: 22px;
    color: var(--card-white);
    font-size: 14px;
  }
  .front-contact .contact-item {
    display: flex;
    align-items: center;
    gap: 6px;
  }
</style>
</head>
<body>
<main class="card-sheet">
  <section class="card card-back" aria-label="Card back">
    <div class="back-glow" role="img" aria-label="Soft orange glow where the brand mark appears"></div>
    <p class="back-website">www.reno7.com.au</p>
  </section>

  <section class="card card-front" aria-label="Card front">
    <svg class="front-waves" viewBox="0 0 540 305" aria-hidden="true">
      <path d="M0,214 C150,168 330,166 540,232 L540,246 C330,196 160,202 0,244 Z" fill="var(--brand-orange)"/>
      <path d="M0,262 C150,226 330,214 540,258 L540,305 L0,305 Z" fill="var(--brand-red)"/>
    </svg>

    <div class="front-brand">
      <span class="brand-square"></span>
      <span class="brand-name">Reno7.com.au</span>
    </div>

    <div class="front-person">
      <p class="person-name">Dean Harwoodson</p>
      <p class="person-role">Project Manager</p>
    </div>

    <div class="front-contact">
      <span class="contact-item">
        <svg width="12" height="12" viewBox="0 0 24 24" aria-hidden="true"><path fill="#fff" d="M6.6 10.8a15.1 15.1 0 0 0 6.6 6.6l2.2-2.2c.3-.3.7-.4 1-.2 1.1.4 2.3.6 3.6.6.6 0 1 .4 1 1V20c0 .6-.4 1-1 1A17 17 0 0 1 3 4c0-.6.4-1 1-1h3.5c.6 0 1 .4 1 1 0 1.3.2 2.5.6 3.6.1.3 0 .7-.2 1z"/></svg>
        0437 916 204
      </span>
      <span class="contact-item">
        <svg width="13" height="10" viewBox="0 0 26 20" aria-hidden="true"><rect x="1" y="1" width="24" height="18" fill="none" stroke="#fff" stroke-width="2"/><path d="M1 1 L13 11 L25 1" fill="none" stroke="#fff" stroke-width="2"/></svg>
        Sales@reno7.com.au
      </span>
    </div>
  </section>
</main>
</body>
</html>
```